VOR Exterior Coatings

double sided. the front i want the name of the business each word on a new line with the VOR being bigger. id like teal, black and white colors. the back i want my contact info. Flat, no gloss. Something professional and I want to feel the letters bump put of the card. if possible maybe a paint sprayer in corner. not a car paint spray. (no tank on top of gun)
no vehicle paint sprayers. that means no tank on top of the gun. doesn't have to have a sprayer. black/dark background on the front. white back ground on back with info

```html
<!DOCTYPE html>
<html lang="en">
<head>
<meta charset="utf-8">
<title>VOR Exterior Coatings – Business Card</title>
<link rel="stylesheet" href="https://fonts.googleapis.com/css2?family=Oswald:wght@600&family=Montserrat:wght@700&family=Arimo:wght@400&display=swap">
<style>
  :root {
    --teal: #14a3a3;
    --teal-deep: #0a6f72;
    --ink: #111111;
    --paper: #ffffff;
    --night: #030708;
    --backdrop: #e6e9ea;
  }
  * { box-sizing: border-box; margin: 0; padding: 0; }
  html, body { width: 1200px; height: 900px; overflow: hidden; }
  body {
    background: var(--backdrop);
    position: relative;
    font-family: "Arimo", Arial, sans-serif;
  }
  .card {
    position: absolute;
    left: 264px;
    width: 672px;
    height: 384px;
    border-radius: 26px;
    overflow: hidden;
    box-shadow: 0 6px 22px rgba(0,0,0,0.18);
  }
  /* front */
  .card--front {
    top: 48px;
    background: radial-gradient(ellipse 62% 80% at 42% 46%, var(--teal-deep) 0%, #06393c 45%, var(--night) 100%);
    display: flex;
    align-items: center;
    justify-content: center;
  }
  .wordmark {
    font-family: "Oswald", "Arial Narrow", sans-serif;
    font-weight: 600;
    text-transform: uppercase;
    line-height: 0.95;
    text-align: center;
  }
  .card--front .wordmark { color: var(--paper); }
  .wordmark__lead { display: block; font-size: 132px; letter-spacing: 4px; }
  .wordmark__line { display: block; font-size: 40px; letter-spacing: 3px; }

  /* back */
  .card--back {
    top: 468px;
    background: var(--paper);
  }
  .card--back .wordmark {
    position: absolute;
    top: 30px;
    left: 0;
    right: 0;
    color: var(--ink);
  }
  .card--back .wordmark__lead { font-size: 78px; letter-spacing: 3px; }
  .card--back .wordmark__line { font-size: 26px; letter-spacing: 2px; display: inline; }
  .card--back .wordmark__line + .wordmark__line { margin-left: 8px; }

  .details {
    position: absolute;
    top: 190px;
    left: 0;
    right: 0;
    display: flex;
    justify-content: center;
    align-items: center;
  }
  .person { text-align: right; padding-right: 22px; }
  .person__name {
    font-family: "Montserrat", Arial, sans-serif;
    font-weight: 700;
    font-size: 27px;
    color: var(--teal);
    letter-spacing: 0.5px;
  }
  .person__role { font-size: 17px; color: var(--ink); margin-top: 2px; }
  .divider { width: 1.5px; height: 78px; background: var(--ink); }
  .contact { list-style: none; padding-left: 22px; }
  .contact__item {
    display: flex;
    align-items: center;
    gap: 10px;
    font-size: 18px;
    color: var(--ink);
    line-height: 1.42;
  }
  .contact__icon { width: 16px; height: 16px; fill: var(--teal); flex: none; }
  .address {
    position: absolute;
    bottom: 48px;
    left: 0;
    right: 0;
    text-align: center;
    font-size: 20px;
    color: var(--ink);
  }
</style>
</head>
<body>
  <section class="card card--front" aria-label="Card front">
    <h1 class="wordmark">
      <span class="wordmark__lead">VOR</span>
      <span class="wordmark__line">Exterior</span>
      <span class="wordmark__line">Coatings</span>
    </h1>
  </section>

  <section class="card card--back" aria-label="Card back">
    <h2 class="wordmark">
      <span class="wordmark__lead">VOR</span>
      <span class="wordmark__line">Exterior</span><span class="wordmark__line">Coatings</span>
    </h2>

    <div class="details">
      <div class="person">
        <p class="person__name">MARCUS REED</p>
        <p class="person__role">Manager</p>
      </div>
      <div class="divider"></div>
      <ul class="contact">
        <li class="contact__item">
          <svg class="contact__icon" viewBox="0 0 16 16" aria-hidden="true"><path d="M3.6 1.2l2.3 2.6-1.3 1.7c.9 2 2.4 3.5 4.4 4.4l1.7-1.3 2.6 2.3-1.4 2.3C6.9 14.8 1.2 9.1 1.3 2.6z"/></svg>
          555-014-2290
        </li>
        <li class="contact__item">
          <svg class="contact__icon" viewBox="0 0 16 16" aria-hidden="true"><path d="M1 3h14v1.2L8 9 1 4.2z M1 5.8L8 10.6l7-4.8V13H1z"/></svg>
          info@vorcoatings.com
        </li>
        <li class="contact__item">
          <svg class="contact__icon" viewBox="0 0 16 16" aria-hidden="true"><path d="M8 1a7 7 0 1 0 0 14A7 7 0 0 0 8 1zm0 2.2a4.8 4.8 0 1 1 0 9.6 4.8 4.8 0 0 1 0-9.6zm0 2a2.8 2.8 0 1 0 0 5.6 2.8 2.8 0 0 0 0-5.6z"/></svg>
          www.vorcoatings.com
        </li>
      </ul>
    </div>

    <p class="address">Your address, city, state, ZIP 0000</p>
  </section>
</body>
</html>
```